Business Card For Halvenmoor Financial Consulting

Hi, I would like a business card designed. Bold, modern.
Please use the same design as the logo. I have also attached the website design to see the overall theme.
Wordmark Font
Color: Hex: #01AEF7

```html
<!DOCTYPE html>
<html lang="en">
<head>
<meta charset="utf-8">
<title>Halvenmoor Financial Consulting – Business Card</title>
<link href="https://fonts.googleapis.com/css2?family=Arimo:wght@400;700&display=swap" rel="stylesheet">
<style>
  :root {
    --brand-blue: #01aef7;
    --card-navy: #111d26;
    --card-navy-deep: #0c161e;
    --stage: #1a1c1f;
    --ink-white: #f2f4f6;
    --ink-muted: #c9d1d8;
    --divider: #5a646c;
  }
  * { margin: 0; padding: 0; box-sizing: border-box; }
  html, body {
    width: 1200px; height: 963px; overflow: hidden;
    background: var(--stage);
    font-family: "Arimo", Arial, sans-serif;
  }
  .sheet {
    width: 1200px; height: 963px;
    display: flex; flex-direction: column; align-items: center; justify-content: center;
    gap: 40px;
  }
  .card {
    position: relative;
    width: 760px; height: 434px;
    background: var(--card-navy);
    border-radius: 26px;
    border-bottom: 4px solid var(--brand-blue);
    overflow: hidden;
  }
  /* Company name set as plain type */
  .company-name {
    position: absolute; left: 0; right: 0; top: 92px;
    text-align: center;
    color: var(--ink-white);
    font-weight: 700; font-size: 38px; letter-spacing: 2px;
    text-transform: uppercase; line-height: 1.1;
  }
  .company-name small {
    display: block; font-size: 15px; letter-spacing: 7px; margin-top: 2px;
  }
  .details {
    position: absolute; left: 0; right: 0; top: 230px;
    display: flex; justify-content: center; align-items: center; gap: 28px;
  }
  .person { text-align: right; }
  .person-name {
    color: var(--brand-blue); font-weight: 700; font-size: 24px;
    text-transform: uppercase; letter-spacing: 0.5px;
  }
  .person-role { color: var(--ink-white); font-size: 17px; margin-top: 4px; }
  .divider { width: 1px; height: 96px; background: var(--divider); }
  .contact-list { list-style: none; }
  .contact-item {
    display: flex; align-items: center; gap: 12px;
    color: var(--ink-white); font-size: 17px; line-height: 30px;
  }
  .contact-icon { width: 16px; height: 16px; flex: none; }
  .address {
    position: absolute; left: 0; right: 0; top: 352px;
    text-align: center; color: var(--ink-muted); font-size: 17px;
  }
  /* Back side */
  .back-texture {
    position: absolute; inset: 0;
    background: linear-gradient(135deg, #16232d 0%, var(--card-navy) 50%, var(--card-navy-deep) 100%);
  }
  .back .company-name { top: 182px; }
</style>
</head>
<body>
<main class="sheet">
  <section class="card front" aria-label="Business card front">
    <p class="company-name">Halvenmoor<small>Financial Consulting</small></p>
    <div class="details">
      <div class="person">
        <p class="person-name">Marcus Delaney</p>
        <p class="person-role">Manager</p>
      </div>
      <span class="divider"></span>
      <ul class="contact-list">
        <li class="contact-item">
          <svg class="contact-icon" viewBox="0 0 16 16"><path fill="#01aef7" d="M3.5 1 6 4 4.6 5.8c.9 2 2.6 3.7 4.6 4.6L11 9l3 2.5-1.3 2.6C7.4 14 2 8.6 1.9 3.3Z"/></svg>
          555-318-7420
        </li>
        <li class="contact-item">
          <svg class="contact-icon" viewBox="0 0 16 16"><rect x="1" y="3" width="14" height="10" rx="1" fill="#01aef7"/><path d="M1.5 3.6 8 9l6.5-5.4" fill="none" stroke="#111d26" stroke-width="1.4"/></svg>
          m.delaney@halvenmoor.com
        </li>
        <li class="contact-item">
          <svg class="contact-icon" viewBox="0 0 16 16"><circle cx="8" cy="8" r="7" fill="#01aef7"/><path d="M1 8h14M8 1c-3 3.5-3 10.5 0 14M8 1c3 3.5 3 10.5 0 14" fill="none" stroke="#111d26" stroke-width="1.2"/></svg>
          www.halvenmoor.com
        </li>
      </ul>
    </div>
    <p class="address">48 Ridgeway Ave, Corvale, State, Zip 0000</p>
  </section>

  <section class="card back" aria-label="Business card back">
    <div class="back-texture" role="img" aria-label="Embossed repeating pattern on dark navy"></div>
    <p class="company-name">Halvenmoor<small>Financial Consulting</small></p>
  </section>
</main>
</body>
</html>
```